A private security company called "Tavron Security Services Ltd"

Hello everybody,

We need a web page for a company based in NZ. It is mainly an informative website so it would be wonderful if the designer puts their absolute best into making it a website that I would really appreciate. The website needs to show professionalism and also needs to make our web surfers find the information they need in a click. the company's colour is black and silver, and if those two colours could be integrated into the website it would be absolutely lovely. Please do contact me for any information.

Sincerely,
Dorian Vaskel

Industry/Entity Type

Security

```html
<!DOCTYPE html>
<html lang="en">
<head>
<meta charset="utf-8">
<title>Tavron Security Services Ltd</title>
<link href="https://fonts.googleapis.com/css2?family=Open+Sans:wght@300;400;600;700&display=swap" rel="stylesheet">
<style>
:root{
  --ink:#1a1a1a;
  --black:#0b0b0b;
  --silver:#d4d4d4;
  --silver-light:#eeeeee;
  --grey-text:#8a8a8a;
  --body-text:#9a9a9a;
  --white:#ffffff;
  --footer-text:#cfcfcf;
}
*{margin:0;padding:0;box-sizing:border-box}
html,body{width:726px;height:1200px;overflow:hidden;background:var(--white);font-family:'Open Sans',sans-serif;color:var(--ink)}
.page{position:relative;width:726px;height:1200px}
.abs{position:absolute}

/* header */
.header{left:54px;top:0;width:618px;height:104px;background:linear-gradient(#fafafa,#f0f0f0)}
.brand{left:67px;top:30px;display:flex;align-items:center;gap:6px}
.brand-mark{width:10px;height:10px;background:var(--ink)}
.brand-name{font-size:11px;font-weight:700;line-height:13px;color:var(--ink);letter-spacing:.3px}
.search{left:490px;top:11px;width:170px;height:23px;border:1px solid #ccc;background:var(--white);font-size:8.5px;color:#aaa;padding:5px 7px}
.search-btn{left:634px;top:11px;width:26px;height:23px;background:var(--ink)}
.phone{right:66px;top:41px;font-size:15.5px;color:#444}
.nav{left:318px;top:69px;display:flex;gap:0;font-size:8.5px;color:var(--ink)}
.nav span{padding:0 9px;line-height:20px}
.nav .active{background:linear-gradient(#444,#111);color:var(--white);border-radius:2px;padding:0 13px}

/* hero */
.hero{left:54px;top:104px;width:618px;height:268px;background:linear-gradient(100deg,#5a5654 0%,#3d3a38 45%,#252322 75%,#1b1a19 100%)}
.hero-box{left:82px;top:166px;width:283px;height:146px;background:rgba(10,10,10,.78);padding:12px 16px}
.hero-title{font-size:25px;font-weight:300;color:var(--white);letter-spacing:-.5px}
.hero-title b{font-weight:600}
.hero-text{margin-top:7px;font-size:7.7px;line-height:12px;color:#ddd}
.btn-light{left:97px;top:274px;width:67px;height:24px;background:linear-gradient(#fff,#d6d6d6);border-radius:2px;font-size:9px;font-weight:600;color:var(--ink);text-align:center;line-height:24px}

/* services */
.service-img{top:372px;width:154.5px;height:126px}
.service-title{top:507px;width:154.5px;text-align:center;font-size:11.5px;font-weight:600;color:#333}
.service-text{top:536px;width:154.5px;padding:0 8px;text-align:center;font-size:7.6px;line-height:12.2px;color:var(--body-text);font-weight:300}

/* newsletter */
.newsletter{left:54px;top:618px;width:618px;height:84px;background:linear-gradient(#e6e6e6,#d2d2d2)}
.email{left:85px;top:652px;width:175px;height:20px;background:var(--white);border-radius:10px 0 0 10px;font-size:7.5px;color:#aaa;padding:5px 10px}
.signup{left:250px;top:652px;width:62px;height:20px;background:linear-gradient(#333,#0a0a0a);border-radius:0 10px 10px 0;font-size:7.5px;color:var(--white);font-weight:600;line-height:20px;padding-left:10px}
.news-title{left:371px;top:643px;font-size:17.5px;font-weight:700;color:var(--ink)}
.news-sub{left:371px;top:667px;font-size:7.2px;color:#444}

/* hire + about */
.hire{left:66px;top:731px;width:276px;height:89px;background:linear-gradient(#4a4a4a,#070707);border-radius:3px;padding:16px 25px;color:var(--white)}
.hire-small{font-size:19px;font-weight:400;line-height:22px}
.hire-big{font-size:28.5px;font-weight:700;line-height:34px}
.section-title{font-size:16px;font-weight:400;color:var(--ink)}
.para{font-size:7.8px;line-height:13.4px;color:var(--body-text);font-weight:300}
.btn-dark{width:75px;height:25px;background:linear-gradient(#444,#0a0a0a);border-radius:2px;font-size:8.5px;color:var(--white);text-align:center;line-height:25px}
.about-img{left:370px;top:756px;width:290px;height:164px;background:linear-gradient(160deg,#6d5a4e 0%,#3a302c 45%,#5b2a22 80%,#2c1d19 100%)}

/* footer */
.footer{left:54px;top:1018px;width:618px;height:182px;background:var(--black)}
.foot-head{top:1037px;font-size:9px;font-weight:700;color:var(--white)}
.foot-list{top:1060px;font-size:7.6px;line-height:12px;color:var(--footer-text);list-style:none}
.foot-list .on{color:var(--white);font-weight:600}
.testimonial{left:333px;top:1062px;width:141px;height:58px;background:var(--white);border-radius:2px;padding:5px 9px;font-size:7px;line-height:12px;color:#aaa;text-align:center}
.field{background:var(--white);font-size:7px;color:#999;padding:3px 5px;border-radius:1px}
.send{left:594px;top:1133px;width:53px;height:19px;background:linear-gradient(#fff,#cfcfcf);border-radius:2px;font-size:8.5px;color:var(--ink);text-align:center;line-height:19px;font-weight:600}
.foot-rule{left:66px;top:1170px;width:594px;height:1px;background:#222}
.copyright{left:54px;top:1178px;width:618px;text-align:center;font-size:7px;color:var(--footer-text)}
</style>
</head>
<body>
<div class="page">

  <header class="abs header"></header>
  <div class="abs brand">
    <span class="brand-mark"></span>
    <span class="brand-name">TAVRON<br>Security Services Ltd.</span>
  </div>
  <div class="abs search">Search</div>
  <div class="abs search-btn">
    <svg width="26" height="23" viewBox="0 0 26 23"><circle cx="12" cy="10.5" r="4.5" fill="none" stroke="#fff" stroke-width="1.8"/><line x1="15.2" y1="13.7" x2="18.5" y2="17" stroke="#fff" stroke-width="2"/></svg>
  </div>
  <div class="abs phone">Call: 123 456 7890</div>
  <nav class="abs nav">
    <span class="active">Home</span><span>About Us</span><span>Security Services</span><span>Why Us</span><span>Testimonials</span><span>Contct Us</span>
  </nav>

  <section class="abs hero" role="img" aria-label="Security guard with a patrol dog at a building entrance at night"></section>
  <div class="abs hero-box">
    <div class="hero-title">WE <b>SECURE</b> YOUR LIFE</div>
    <p class="hero-text">Lorem ipsum dolor sit amet, consectetur adipisicing elit, sed eiusmod tempor incididunt ut labore et dolore magna aliqua ut enim ad minim veniam, quis nostrud exercitation ullamco laborisnisi ut aliquip ex ea commodo consequat.</p>
  </div>
  <div class="abs btn-light">Read More</div>

  <div class="abs service-img" style="left:54px;background:linear-gradient(90deg,#b9c4cc,#7fa0c2 60%,#3b4a6a)" role="img" aria-label="Uniformed guard in a building lobby"></div>
  <div class="abs service-img" style="left:208.5px;background:linear-gradient(180deg,#8a94a0,#d8dadd 55%,#f2f2f2)" role="img" aria-label="Row of patrol cars with light bars"></div>
  <div class="abs service-img" style="left:363px;background:linear-gradient(180deg,#3f86d6,#8fbde6 60%,#5a6b7a)" role="img" aria-label="Security camera over a city skyline"></div>
  <div class="abs service-img" style="left:517.5px;background:linear-gradient(180deg,#aec7e2,#6e8eb0 50%,#2a2a2a)" role="img" aria-label="Armed officer's duty belt and holster"></div>

  <div class="abs service-title" style="left:54px">Guard Services</div>
  <div class="abs service-title" style="left:208.5px">Security Patrols</div>
  <div class="abs service-title" style="left:363px">Fixed Camra Systems</div>
  <div class="abs service-title" style="left:517.5px">Armed Security Officers</div>
  <p class="abs service-text" style="left:54px">Lorem ipsum dolor sit amet, con-sectetur adipisicing elit, sed eiusmod tempor incididunt ut labore et dolore magna aliqua ut enim ad minim.</p>
  <p class="abs service-text" style="left:208.5px">Lorem ipsum dolor sit amet, con-sectetur adipisicing elit, sed eiusmod tempor incididunt ut labore et dolore magna aliqua ut enim ad minim.</p>
  <p class="abs service-text" style="left:363px">Lorem ipsum dolor sit amet, con-sectetur adipisicing elit, sed eiusmod tempor incididunt ut labore et dolore magna aliqua ut enim ad minim.</p>
  <p class="abs service-text" style="left:517.5px">Lorem ipsum dolor sit amet, con-sectetur adipisicing elit, sed eiusmod tempor incididunt ut labore et dolore magna aliqua ut enim ad minim.</p>

  <section class="abs newsletter"></section>
  <div class="abs email">Whats your Email Address?</div>
  <div class="abs signup">SIGN UP &#8594;</div>
  <div class="abs news-title">SUBSRIBE TO OUR NEWSLATTER</div>
  <div class="abs news-sub">LOREM IPSUM DOLOR SIT AMET, CONSECTETUR ELIT, <b>SED EIUSMOD TEMPOR</b></div>

  <div class="abs hire">
    <div class="hire-small">GET SECURED NOW</div>
    <div class="hire-big">HIRE US TODAY!</div>
  </div>
  <svg class="abs" style="left:297px;top:820px" width="18" height="17" viewBox="0 0 18 17"><rect x="6" y="0" width="6" height="8" fill="#0b0b0b"/><polygon points="0,8 18,8 9,17" fill="#0b0b0b"/></svg>
  <h2 class="abs section-title" style="left:66px;top:846px">Experience Matters</h2>
  <p class="abs para" style="left:66px;top:873px;width:276px">Lorem ipsum dolor sit ame cnsectetur adipisicing elit sed eiusmod tempor incididunt ut labore et dolore magna aliqua ut enim ad minim. veniam, quis nostrud exercitation ullamco laborisnisi ut aliquip ex commodo consequat duis aute irure dolor in reprehenderit in voluptate velit ess cillum dolore eu fugiat nulla pariatur excepteur sint occaecat cupidatat non proident sunt in culpa qui officia deserunt mollit anim id est laborum</p>
  <div class="abs btn-dark" style="left:66px;top:970px">Read More</div>

  <h2 class="abs section-title" style="left:372px;top:727px">About Us</h2>
  <div class="abs about-img" role="img" aria-label="Staff at monitoring desks in a security control room"></div>
  <p class="abs para" style="left:370px;top:928px;width:290px">Lorem ipsum dolor sit ame cnsectetur adipisicing elit sed eiusmod tempor culpa qui officia deserunt mollit anim id est laborum</p>
  <div class="abs btn-dark" style="left:369px;top:970px">Read More</div>

  <footer class="abs footer"></footer>
  <div class="abs foot-head" style="left:80px">SITE MAP</div>
  <ul class="abs foot-list" style="left:80px">
    <li class="on">Home</li><li>About Us</li><li>Security Services</li><li>Why Us</li><li>Testimonials</li><li>Contct Us</li>
  </ul>
  <div class="abs foot-head" style="left:190px">LINKS</div>
  <ul class="abs foot-list" style="left:191px;line-height:13.3px">
    <li>Lorem ipsum dolor sit</li><li>Ame cnsectetur adipisicing</li><li>Elit sed eiusmod tempor</li><li>Incididunt ut labore et</li><li>Dolore magna</li>
  </ul>
  <div class="abs foot-head" style="left:333px">TESTIMONIALS</div>
  <div class="abs testimonial">Lorem ipsum dolor sit ame cnsecte-tur adipisicing elit eiusmod tempor incididunt ut labore et dolore magna aliqua ut enim ad minim. veniam.</div>
  <div class="abs foot-head" style="left:518px;top:1036px">QUICK CONTACT</div>
  <div class="abs field" style="left:518px;top:1062px;width:129px;height:18px">Email Adderss</div>
  <div class="abs field" style="left:518px;top:1084px;width:129px;height:40px">Massage</div>
  <div class="abs send">SEND</div>
  <div class="abs foot-rule"></div>
  <div class="abs copyright">Copy rigthe 2014 &copy;. Tavron Security . All rights reserved</div>

</div>
</body>
</html>
```